verdant terraces simple classy business card design

my name is colin barrow and I run a gardening business aimed at high class verdant terraces. the business name is verdant terraces and our logo was designed on pixel harbour .My clientel are anything from residential homes to businesses. I take pride in my work and know that I offer a service like no other in my area.
The business card will be used to represent my business and I want it to be not only rememberable, but simplistic and modern. Eye catching too. Of course I would like it relatable to gardening and appealing to the correct clientel - those being garden enthusiasts, prestigious homes and businesses that are after top of the line gardening services like no other on the market.
I am not a typical lawn mowing business so I don't want a typical card design that represents that. The gardens I work with are generally million dollar properties with owners who are very garden proud looking for upkeep and guidance from me along with sometimes whole new garden designs. I want the business cards to show to my clients that I take pride, as they do, in their garden. And I want them to know from my card that I am a professional, qualified horticulturist offering them a top of the line service for life. I want them to refer my business on. I want them to look at my business card and see class and professionalism in a modern unique bold way.
The card should be simple with the possibility of the logo on the front being embossed/debossed and my details on the back the card should have a organic garden feel it's very important to me that it is absolutely perfect
I am also very open to ideas and suggestions so look forward to seeing the designs. the business logo has been supplied with this project and I want the card to be double sided

Contact info is
Colin Barrow - Managing Director / Horticulturist
Phone : 0481 526 704
Email: colinbarrow@verdantterraces.example.au

Target Market(s)

high class gardens residential and commercial

Industry/Entity Type

Gardener

Contact Information for Business Card

Contact info is
Phone : 0481 526 704

PLEASE MAKE CARD DOUBLE SIDED

Requirements
Must have
• organic simple classy modern feel
• must flow with the current logo that has been supplied with this project
• Double sided
• Must explain in a simple way that I deal with high end gardens and I'm a qualified horticulturist
Nice to have
• embossed debossed logo
Should not have
• shouldn't be to busy or cheap looking

```html
<!DOCTYPE html>
<html lang="en">
<head>
<meta charset="utf-8">
<title>Verdant Terraces – Business Card</title>
<link rel="stylesheet" href="https://fonts.googleapis.com/css2?family=Cinzel:wght@500&family=Arimo:wght@400;700&display=swap">
<style>
  :root {
    --leaf-green: #4b8d3c;
    --leaf-green-soft: #d9e8d2;
    --paper: #f7f7f4;
    --ink: #262626;
    --ink-muted: #555555;
    --backdrop: #e9e6e1;
  }
  * { box-sizing: border-box; margin: 0; padding: 0; }
  html, body { width: 1200px; height: 794px; overflow: hidden; }
  body {
    background: var(--backdrop);
    display: flex;
    align-items: center;
    justify-content: center;
    gap: 40px;
    font-family: "Arimo", Arial, sans-serif;
  }
  .card {
    width: 540px;
    height: 330px;
    position: relative;
    box-shadow: 0 6px 18px rgba(0,0,0,0.12);
    overflow: hidden;
  }

  /* Front */
  .card-front {
    background: var(--leaf-green);
    display: flex;
    flex-direction: column;
    align-items: center;
    justify-content: center;
    gap: 14px;
  }
  .brand-dot {
    width: 54px;
    height: 54px;
    border-radius: 50%;
    background: var(--paper);
  }
  .wordmark {
    font-family: "Cinzel", Georgia, serif;
    font-weight: 500;
    text-align: center;
    line-height: 1.15;
    letter-spacing: 0.12em;
  }
  .card-front .wordmark { color: var(--paper); font-size: 30px; }

  /* Back */
  .card-back { background: var(--paper); }
  .card-back .brand-circle {
    position: absolute;
    left: 44px;
    top: 58px;
    width: 210px;
    height: 210px;
    border-radius: 50%;
    background: var(--leaf-green-soft);
  }
  .contact {
    position: absolute;
    right: 34px;
    top: 46px;
    text-align: right;
  }
  .contact-name {
    color: var(--leaf-green);
    font-weight: 700;
    font-size: 19px;
    letter-spacing: 0.03em;
    text-transform: uppercase;
    margin-bottom: 6px;
  }
  .contact-role {
    color: var(--ink);
    font-size: 14px;
    margin-bottom: 10px;
  }
  .contact-phone {
    color: var(--leaf-green);
    font-size: 13px;
    margin-bottom: 12px;
  }
  .contact-line {
    color: var(--ink-muted);
    font-size: 12px;
    line-height: 1.5;
  }
  .card-back .wordmark {
    position: absolute;
    right: 34px;
    bottom: 38px;
    color: var(--leaf-green);
    font-size: 27px;
    text-align: right;
  }
  .base-band {
    position: absolute;
    left: 0;
    right: 0;
    bottom: 0;
    height: 20px;
    background: var(--leaf-green);
  }
</style>
</head>
<body>
  <section class="card card-front" aria-label="Card front">
    <div class="brand-dot"></div>
    <p class="wordmark">VERDANT<br>TERRACES</p>
  </section>

  <section class="card card-back" aria-label="Card back">
    <div class="brand-circle"></div>
    <div class="contact">
      <p class="contact-name">Colin Barrow</p>
      <p class="contact-role">Managing Director / Horticulturist</p>
      <p class="contact-phone">P : 0481 526 704</p>
      <p class="contact-line">colinbarrow@verdantterraces.example.au</p>
      <p class="contact-line">verdantterraces.example.au</p>
    </div>
    <p class="wordmark">VERDANT<br>TERRACES</p>
    <div class="base-band"></div>
  </section>
</body>
</html>
```